Revise Three Graphics for Company Careers website.

We have a need to find an alternative artistic approach to revising three graphics currently used on a growing companies careers/job website.
- The new art for attached graphics (named graphic #1, #2, and #3) should be clean, professional and easy to read.
- The art representing these three pieces should share common artistic elements and not necessarily look like three differently branded pieces.
- The careers site is shared between two related companies, so the colors used should complement the colors of two companies (whose logos are attached).
- Logos can be used as knock-outs if needed.
Note: Graphic #3 (currently a set of boxes 2x3) needs two additional boxes with the following copy:
- Art and Science of Communication
- Supervising 101
Lastly, Graphic #4 we need to be put into the same color font used in the two company logos. That's it!

```html
<!DOCTYPE html>
<html lang="en">
<head>
<meta charset="utf-8">
<title>Professional Development Programs</title>
<link rel="stylesheet" href="https://fonts.googleapis.com/css2?family=Open+Sans:wght@400;600&display=swap">
<style>
  :root {
    --bg: #ffffff;
    --blue: #1766d6;
    --red: #ef1b24;
    --lime: #a5e01d;
    --mint: #70fde0;
    --ring: #d9dde3;
    --navy: #1b2c6b;
    --ink: #111111;
    --on-color: #ffffff;
  }
  html, body {
    margin: 0;
    padding: 0;
    width: 1200px;
    height: 605px;
    overflow: hidden;
    background: var(--bg);
  }
  .program-grid {
    display: block;
    width: 1200px;
    height: 605px;
    font-family: "Open Sans", "Segoe UI", sans-serif;
  }
  .badge { stroke: none; }
  .badge--blue { fill: var(--blue); }
  .badge--red { fill: var(--red); }
  .badge--lime { fill: var(--lime); }
  .badge--mint { fill: var(--mint); }
  .badge--outline { fill: var(--bg); stroke: var(--ring); stroke-width: 4; }
  .badge-label {
    font-size: 28px;
    font-weight: 600;
    text-anchor: middle;
    dominant-baseline: middle;
  }
  .label--light { fill: var(--on-color); }
  .label--navy { fill: var(--navy); }
  .label--ink { fill: var(--ink); font-weight: 400; }
</style>
</head>
<body>
<svg class="program-grid" viewBox="0 0 1200 605" role="list" aria-label="Professional development programs">
  <defs>
    <filter id="soft-lift" x="-20%" y="-20%" width="140%" height="140%">
      <feDropShadow dx="0" dy="2" stdDeviation="3" flood-color="#000" flood-opacity="0.12"/>
    </filter>
  </defs>

  <!-- Row one -->
  <g role="listitem">
    <circle class="badge badge--blue" cx="151" cy="160" r="142"/>
    <text class="badge-label label--light" x="151" y="160">
      <tspan x="151" dy="-18">Scientific Lunch</tspan><tspan x="151" dy="36">and Learns</tspan>
    </text>
  </g>
  <g role="listitem">
    <circle class="badge badge--outline" cx="443" cy="160" r="140" filter="url(#soft-lift)"/>
    <text class="badge-label label--navy" x="443" y="160">
      <tspan x="443" dy="-54">Statistics in</tspan><tspan x="443" dy="36">Pharmaceutical</tspan><tspan x="443" dy="36">Development</tspan><tspan x="443" dy="36">Workshop</tspan>
    </text>
  </g>
  <g role="listitem">
    <circle class="badge badge--red" cx="771" cy="160" r="142"/>
    <text class="badge-label label--light" x="771" y="160">
      <tspan x="771" dy="-18">Conferences and</tspan><tspan x="771" dy="36">Seminars</tspan>
    </text>
  </g>
  <g role="listitem">
    <circle class="badge badge--outline" cx="1061" cy="160" r="140" filter="url(#soft-lift)"/>
    <text class="badge-label label--navy" x="1061" y="160">
      <tspan x="1061" dy="-18">Leadership</tspan><tspan x="1061" dy="36">Development</tspan>
    </text>
  </g>

  <!-- Row two -->
  <g role="listitem">
    <circle class="badge badge--outline" cx="151" cy="458" r="140" filter="url(#soft-lift)"/>
    <text class="badge-label label--navy" x="151" y="458">
      <tspan x="151" dy="-18">Creating the Right</tspan><tspan x="151" dy="36">Team Workshop</tspan>
    </text>
  </g>
  <g role="listitem">
    <circle class="badge badge--lime" cx="443" cy="458" r="142"/>
    <text class="badge-label label--light" x="443" y="458">
      <tspan x="443" dy="-36">Project</tspan><tspan x="443" dy="36">Management</tspan><tspan x="443" dy="36">Training</tspan>
    </text>
  </g>
  <g role="listitem">
    <circle class="badge badge--outline" cx="771" cy="458" r="140" filter="url(#soft-lift)"/>
    <text class="badge-label label--ink" x="771" y="458">
      <tspan x="771" dy="-18">Art &amp; Science of</tspan><tspan x="771" dy="36">Communication</tspan>
    </text>
  </g>
  <g role="listitem">
    <circle class="badge badge--mint" cx="1061" cy="458" r="142"/>
    <text class="badge-label label--light" x="1061" y="458">Supervising 101</text>
  </g>
</svg>
</body>
</html>
```